Business Card Design for a Software Startup

We'd like to have a business card design. We already have a logo. Basically what we need is a clean design with name, address, cellphone and phone numbers, e-mail and web site address (front) and a space on the back with our logo with the company name on the right side and some texts on the bottom.
We are a development and consulting company in Brazil with highly qualified team of professionals in Java, iOS and Android development and consulting.

Target Market(s)

CIO, IT managers of mid to big size companies

Industry/Entity Type

Business

```html
<!DOCTYPE html>
<html lang="en">
<head>
<meta charset="utf-8">
<title>ORVELIX Business Card</title>
<link rel="stylesheet" href="https://fonts.googleapis.com/css2?family=Arimo:wght@400;700&family=Questrial&display=swap">
<style>
  :root {
    --navy: #1f3f7c;
    --navy-deep: #2a2f6e;
    --cyan: #0ba3e0;
    --sky: #3bb6ea;
    --ink: #3a3f4a;
    --muted: #6b7280;
    --paper: #ffffff;
    --stage: #e9ebef;
    --rule: #b9c0cc;
  }
  * { margin: 0; padding: 0; box-sizing: border-box; }
  html, body {
    width: 1200px;
    height: 720px;
    overflow: hidden;
    background: var(--stage);
  }
  .card {
    position: absolute;
    top: 205px;
    width: 540px;
    height: 309px;
    overflow: hidden;
    box-shadow: 0 4px 14px rgba(0,0,0,0.12);
  }

  /* Front */
  .card-front { left: 40px; background: var(--paper); }
  .front-top-band {
    position: absolute; left: 0; top: 0; width: 100%; height: 46px;
  }
  .front-bottom-band {
    position: absolute; left: 0; bottom: 0; width: 100%; height: 52px;
    background: var(--navy);
    border-top: 6px solid var(--sky);
  }
  .front-address {
    position: absolute; left: 0; bottom: 15px; width: 100%;
    text-align: center;
    font: 400 13px "Questrial", sans-serif;
    letter-spacing: 0.4px;
    color: var(--paper);
  }
  .brand-name {
    position: absolute; left: 0; top: 68px; width: 100%;
    text-align: center;
    font: 700 34px "Arimo", sans-serif;
    color: var(--navy);
    letter-spacing: 1px;
  }
  .person {
    position: absolute; right: 290px; top: 170px;
    text-align: right;
    font-family: "Arimo", sans-serif;
  }
  .person-name { font-weight: 700; font-size: 21px; color: var(--navy); }
  .person-title { font-size: 12px; color: var(--muted); margin-top: 1px; }
  .divider {
    position: absolute; left: 262px; top: 140px; width: 1px; height: 100px;
    background: var(--rule);
  }
  .contact-list {
    position: absolute; left: 274px; top: 140px;
    list-style: none;
    font: 400 13px "Questrial", sans-serif;
    color: var(--ink);
    line-height: 20px;
  }
  .contact-label { color: var(--cyan); margin-right: 4px; }

  /* Back */
  .card-back {
    left: 620px;
    background: radial-gradient(circle at 48% 42%, #0fa0dc 0%, #1672b4 28%, #27448a 55%, var(--navy-deep) 80%);
  }
  .back-name {
    position: absolute; left: 0; top: 108px; width: 100%;
    text-align: center;
    font: 700 46px "Arimo", sans-serif;
    color: var(--paper);
    letter-spacing: 2px;
  }
  .back-web {
    position: absolute; left: 0; bottom: 46px; width: 100%;
    text-align: center;
    font: 700 16px "Arimo", sans-serif;
    color: var(--paper);
    letter-spacing: 5px;
  }
</style>
</head>
<body>
  <section class="card card-front">
    <svg class="front-top-band" viewBox="0 0 540 46" preserveAspectRatio="none">
      <defs>
        <linearGradient id="topBand" x1="0" y1="0" x2="1" y2="0">
          <stop offset="0" stop-color="#243c7c"/>
          <stop offset="0.6" stop-color="#1e6cb3"/>
          <stop offset="1" stop-color="#22b0ea"/>
        </linearGradient>
      </defs>
      <polygon points="0,0 540,0 540,22 380,22 350,46 0,46" fill="url(#topBand)"/>
    </svg>

    <div class="brand-name">ORVELIX</div>

    <div class="person">
      <div class="person-name">Your Name</div>
      <div class="person-title">Title</div>
    </div>
    <div class="divider"></div>
    <ul class="contact-list">
      <li><span class="contact-label">p:</span>123-456-7890</li>
      <li><span class="contact-label">c:</span>123-456-7890</li>
      <li><span class="contact-label">e:</span>yourname@orvelix-dev.com</li>
      <li><span class="contact-label">w:</span>www.orvelix-dev.com</li>
    </ul>

    <div class="front-bottom-band"></div>
    <p class="front-address">Door No. Street Name City Name, State, Zip Code.</p>
  </section>

  <section class="card card-back">
    <div class="back-name">ORVELIX</div>
    <p class="back-web">www.orvelix-dev.com</p>
  </section>
</body>
</html>
```